German Headhunter/ HR Consultancy needs Business Cards Design

We need a business Card Design for our Company in Stuttgart. We are specialized as Headhunter/ HR Consultancy in Placement of specialist and managers in permanent employment. Please refer to our business logo.

```html
<!DOCTYPE html>
<html lang="de">
<head>
<meta charset="utf-8">
<title>Kernwerk Personalberatung – Visitenkarte</title>
<link rel="stylesheet" href="https://fonts.googleapis.com/css2?family=Montserrat:wght@400;500;700&display=swap">
<style>
  :root {
    --bg: #c9c9c9;
    --card: #232323;
    --card-deep: #151515;
    --blue: #3b55c4;
    --grey: #a9a9a9;
    --text-light: #d4d4d4;
    --rule: #5a5a5a;
  }
  * { box-sizing: border-box; margin: 0; padding: 0; }
  html, body { width: 1200px; height: 800px; overflow: hidden; }
  body {
    background: var(--bg);
    font-family: "Montserrat", Arial, sans-serif;
    display: flex;
    align-items: center;
    justify-content: center;
    gap: 40px;
  }
  .card {
    position: relative;
    width: 540px;
    height: 310px;
    background: var(--card);
    border-bottom: 3px solid var(--blue);
    box-shadow: 0 14px 30px rgba(0,0,0,0.35);
    overflow: hidden;
  }
  .brand {
    display: flex;
    align-items: center;
    gap: 12px;
    color: var(--blue);
    font-weight: 700;
    letter-spacing: 1px;
  }
  .brand-square {
    width: 26px; height: 26px;
    background: var(--blue);
    flex: none;
  }
  .card-front .brand {
    position: absolute;
    top: 48px; right: 40px;
    font-size: 19px;
  }
  .card-front .divider {
    position: absolute;
    left: 40px; right: 40px; top: 150px;
    height: 1px;
    background: var(--rule);
  }
  .person {
    position: absolute;
    left: 40px; top: 176px;
  }
  .person-name {
    color: var(--blue);
    font-weight: 700;
    font-size: 19px;
    letter-spacing: 0.5px;
    text-transform: uppercase;
  }
  .person-title {
    color: var(--grey);
    font-size: 13px;
    margin-top: 3px;
  }
  .person-rule {
    width: 220px; height: 1px;
    background: var(--rule);
    margin: 12px 0 10px;
  }
  .contact-list { list-style: none; }
  .contact-list li {
    display: flex;
    align-items: center;
    gap: 8px;
    color: var(--text-light);
    font-size: 13px;
    line-height: 20px;
  }
  .contact-list svg { width: 13px; height: 13px; fill: var(--blue); flex: none; }
  .contact-list .accent { color: var(--blue); }
  .address {
    position: absolute;
    right: 40px; top: 176px;
    text-align: right;
    color: var(--text-light);
    font-size: 13px;
    line-height: 20px;
  }
  .card-back .pattern {
    position: absolute;
    inset: 0;
    background: linear-gradient(135deg, var(--card-deep) 0%, #1e1e1e 55%, #3a3a3a 100%);
  }
  .card-back .brand {
    position: absolute;
    right: 48px; bottom: 60px;
    font-size: 19px;
  }
</style>
</head>
<body>

  <section class="card card-front" aria-label="Vorderseite">
    <div class="brand">
      <span class="brand-square"></span>
      <span class="brand-name">KERNWERK PERSONALBERATUNG</span>
    </div>
    <div class="divider"></div>

    <div class="person">
      <p class="person-name">Lukas Brenner</p>
      <p class="person-title">Managing Director</p>
      <div class="person-rule"></div>
      <ul class="contact-list">
        <li>
          <svg viewBox="0 0 24 24" aria-hidden="true"><path d="M6.6 10.8a15.1 15.1 0 0 0 6.6 6.6l2.2-2.2c.3-.3.7-.4 1-.2 1.1.4 2.3.6 3.6.6.6 0 1 .4 1 1V20c0 .6-.4 1-1 1A17 17 0 0 1 3 4c0-.6.4-1 1-1h3.5c.6 0 1 .4 1 1 0 1.3.2 2.5.6 3.6.1.3 0 .7-.2 1z"/></svg>
          0711-555 208 14
        </li>
        <li>
          <svg viewBox="0 0 24 24" aria-hidden="true"><path d="M2 5h20v14H2z M2 5l10 8 10-8" /></svg>
          info@kernwerk-hr.de
        </li>
        <li>
          <svg viewBox="0 0 24 24" aria-hidden="true"><path d="M12 2a10 10 0 1 0 0 20 10 10 0 0 0 0-20zm6.9 6h-3a15 15 0 0 0-1.3-4 8 8 0 0 1 4.3 4zM12 4c.8 1.2 1.5 2.5 1.9 4h-3.8c.4-1.5 1.1-2.8 1.9-4zM4.3 14a8 8 0 0 1 0-4h3.4a16 16 0 0 0 0 4zm.8 2h3a15 15 0 0 0 1.3 4 8 8 0 0 1-4.3-4zm3-8h-3a8 8 0 0 1 4.3-4 15 15 0 0 0-1.3 4zM12 20c-.8-1.2-1.5-2.5-1.9-4h3.8c-.4 1.5-1.1 2.8-1.9 4zm2.3-6H9.7a14 14 0 0 1 0-4h4.6a14 14 0 0 1 0 4zm.3 6a15 15 0 0 0 1.3-4h3a8 8 0 0 1-4.3 4zm1.7-6a16 16 0 0 0 0-4h3.4a8 8 0 0 1 0 4z"/></svg>
          <span>www.<span class="accent">kernwerk-hr</span>.de</span>
        </li>
      </ul>
    </div>

    <address class="address" style="font-style: normal;">
      12 Königsallee Ost<br>
      70173 Stuttgart
    </address>
  </section>

  <section class="card card-back" aria-label="Rückseite">
    <div class="pattern" role="img" aria-label="Tonal embossed repeat pattern of the brand mark across the card"></div>
    <div class="brand">
      <span class="brand-square"></span>
      <span class="brand-name">KERNWERK PERSONALBERATUNG</span>
    </div>
  </section>

</body>
</html>
```